Dale Harlow Sausage Label Design

Halvern Fields Corporation is seeking to create a new brand of fresh 100% Canadian pork sausage. This label will be a paper band that slips on and off foam trays. The front facing side will be 5 inches wide by 3.5 inches high. The following is some information about our brand.
Target market:
1. Working Moms
2. Stay at home moms
3. Barbeque enthusiast
Brand personality
1. Old school values – We are a family run company who believes in an honest days work
2. Modern day sensibility – We believe in being nimble and open to new ideas
3. Energetic and optimistic – We are passionate about our business and product
4. Relaxed sense of humor – We believe that it is possible to work hard and have fun
Positioning Statements:
Our sausage is the easy choice for adding flavour to your real- life family meals, that’s because:
1. It is 100% fresh Canadian product with no fillers or preservatives
2. It is a great tasting recipe with simple, natural ingredients
3. It is brought to you with good humor and integrity by a multi- generational family owned business
We are looking for a creative designer to make our ideas come to life. There are three types of designs we would like to see:
1. Rustic – a rustic, barbequing, old farm, country feel – without feeling too old
2. Modern & Simple – Very simple clean face with clean text
3. Family friendly – a label that would appeal to the everyday family with photos of the finished product
This brand does not have a name yet, please use the name “Dale Harlow “as a place holder. Please keep in mind the information provided about our brand when developing the label. Attached are pictures of some ideas we like. Please do not copy these ideas too closely, we are looking to differentiate ourselves in the market. Samples are to provide some guidance of our preferences.
Target Market(s)
1. Working Moms
2. Stay at home moms
3. Barbeque enthusiast
Colors
Designer to choose colors to be used in the design.

```html
<!DOCTYPE html>
<html lang="en">
<head>
<meta charset="utf-8">
<title>Dale Harlow Sausage Label</title>
<link rel="stylesheet" href="https://fonts.googleapis.com/css2?family=Roboto+Slab:wght@700;800;900&family=Damion&display=swap">
<style>
  :root {
    --label-orange: #da862e;
    --label-brown: #5e3a16;
    --label-cream: #eeefde;
  }
  html, body {
    margin: 0;
    padding: 0;
    overflow: hidden;
    background: var(--label-orange);
  }
  .label {
    position: relative;
    width: 1200px;
    height: 843px;
    background: var(--label-orange);
    overflow: hidden;
    font-family: "Roboto Slab", "Rockwell", serif;
    font-weight: 700;
    color: var(--label-cream);
  }
  .brand-name {
    position: absolute;
    left: 40px;
    margin: 0;
    line-height: 1;
    font-weight: 800;
    color: var(--label-cream);
    white-space: nowrap;
  }
  .brand-first { top: 12px; font-size: 252px; letter-spacing: -4px; }
  .brand-last { top: 255px; font-size: 190px; letter-spacing: -3px; }
  .fork-art {
    position: absolute;
    left: 820px;
    top: 104px;
    width: 336px;
    height: 132px;
  }
  .rule {
    position: absolute;
    background: var(--label-cream);
  }
  .rule-top { left: 42px; top: 456px; width: 1114px; height: 4px; }
  .rule-mid { left: 408px; top: 540px; width: 748px; height: 4px; }
  .rule-bottom { left: 42px; top: 688px; width: 1114px; height: 4px; }
  .rule-v-main { left: 406px; top: 460px; width: 4px; height: 336px; }
  .rule-v-count { left: 160px; top: 692px; width: 4px; height: 104px; }
  .origin-map {
    position: absolute;
    left: 64px;
    top: 476px;
    width: 236px;
    height: 192px;
  }
  .origin-claim {
    position: absolute;
    left: 250px;
    top: 476px;
    margin: 0;
    font-family: "Damion", cursive;
    font-weight: 400;
    font-size: 34px;
    line-height: 0.95;
    color: var(--label-cream);
    transform: rotate(-4deg);
  }
  .text {
    position: absolute;
    margin: 0;
    line-height: 1;
    white-space: nowrap;
  }
  .producer { left: 437px; top: 487px; font-size: 27px; }
  .flavour { left: 430px; top: 562px; font-size: 59px; font-weight: 900; color: var(--label-brown); }
  .product-type { left: 438px; top: 630px; font-size: 34px; }
  .pack-count { left: 70px; top: 726px; font-size: 31px; }
  .weight { left: 194px; top: 716px; font-size: 34px; }
  .weight .estimate-mark { font-family: Georgia, serif; font-size: 42px; font-weight: normal; margin-left: 8px; vertical-align: -4px; }
  .storage { left: 194px; top: 756px; font-size: 17px; }
  .description { left: 438px; top: 708px; font-size: 34px; line-height: 42px; }
</style>
</head>
<body>
<main class="label">
  <h1 class="brand-name brand-first">DALE</h1>
  <h1 class="brand-name brand-last">HARLOW</h1>

  <svg class="fork-art" role="img" aria-label="Illustration of a fork pointing left beside the brand name" viewBox="0 0 336 132">
    <defs>
      <linearGradient id="forkTone" x1="0" y1="0" x2="1" y2="0">
        <stop offset="0" stop-color="#5e3a16" stop-opacity="0.15"/>
        <stop offset="0.5" stop-color="#5e3a16" stop-opacity="0.45"/>
        <stop offset="1" stop-color="#5e3a16" stop-opacity="0.15"/>
      </linearGradient>
    </defs>
    <rect x="0" y="0" width="336" height="132" rx="20" fill="url(#forkTone)"/>
  </svg>

  <div class="rule rule-top"></div>
  <div class="rule rule-mid"></div>
  <div class="rule rule-bottom"></div>
  <div class="rule rule-v-main"></div>
  <div class="rule rule-v-count"></div>

  <svg class="origin-map" role="img" aria-label="Map of Canada silhouette" viewBox="0 0 236 192">
    <defs>
      <radialGradient id="mapTone" cx="0.5" cy="0.5" r="0.6">
        <stop offset="0" stop-color="#eeefde" stop-opacity="0.85"/>
        <stop offset="1" stop-color="#eeefde" stop-opacity="0.35"/>
      </radialGradient>
    </defs>
    <rect x="0" y="0" width="236" height="192" rx="18" fill="url(#mapTone)"/>
  </svg>
  <p class="origin-claim">100%<br>Canadian</p>

  <p class="text producer">HALVERN FIELDS CORPORATION</p>
  <h2 class="text flavour">MUTTON &amp; MINT</h2>
  <p class="text product-type">PORK SAUSAGES</p>

  <p class="text pack-count">X6</p>
  <p class="text weight">400G<span class="estimate-mark">℮</span></p>
  <p class="text storage">KEEP REFRIGERATED</p>
  <p class="text description">6 MATURE MUTTON&nbsp; SAUSAGE,<br>INFUSED WITH MINT.</p>
</main>
</body>
</html>
```